2018 Desk Calendar Design with Better Spine, Better Health with Chiropractic

In conjunction with the Federation of Spinal Wellness Malaysia (FSW), we are organizing a 2018 desk calendar design. The cover page and monthly design size is 210mm (H) x 195mm (W). The will be a total of 27 designs including a cover page (front) [Sample 1], cover page (back) Malaysia National & States Holiday 2018 (https://restdaylist.example.my/2018-dates/) [Sample 2], 12 months design (front) [Sample 3 and 4], 12 months design (back) [Sample 5], Last page (2017 and 2019 calendar) [Sample 6].

Below are some recommendations for monthly back cover design. The main theme remain as Better SPINE, Better HEALTH with CHIROPRACTIC. Each month can in collaborate with of the following element:-

Suggestion 1 (Celebration of the Month)
January - New Year
February - Chinese New Year
March -
April -
May - Labour Day
June - Aidilfitri Festival
July-
August - Independent Day
September - Malaysia Day
October - World Spine Day
November - Deepavali Festival
December - Christmas

Suggestion 2 (States in Malaysia)
January - Perlis
February - Kedah
March - Penang
April - Perak
May - Selangor
June - Negeri Sembilan
July- Melaka
August - Johor
September - Pahang
October - Terengganu
November - Kelantan
December - Sabah & Sarawak

Target Market(s)

Chiropractors and Public

Industry/Entity Type

Chiropractor

Colors

Designer to choose colors to be used in the design.

Requirements
Must have
• The theme for the desk calendar design is Better Spine, Better Health with Chiropractic.
• The cover page should include 5th Anniversary element.
Nice to have
• Lunar or Islamic calendar is optional in the Gregorian calendar.
• AI Format
• Footnote of each page www.spinefsw.example.org

```html
<!DOCTYPE html>
<html lang="en">
<head>
<meta charset="utf-8">
<title>June 2018 – Desk Calendar</title>
<link rel="stylesheet" href="https://fonts.googleapis.com/css2?family=Michroma&family=Libre+Baskerville:wght@700&family=Open+Sans:wght@400&display=swap">
<style>
  :root {
    --paper: #b2adb6;
    --photo-light: #aaaaaa;
    --photo-dark: #7f7f7f;
    --band-light: #9a5fa0;
    --band-mid: #7b3f7f;
    --vertebra: #4f1c53;
    --vertebra-soft: #5d2462;
    --title: #4f2350;
    --ink: #111111;
    --sunday: #e0202a;
    --rule: #5a2a5c;
    --white: #ffffff;
    --badge: #2b3a8f;
  }
  * { margin: 0; padding: 0; box-sizing: border-box; }
  html, body { width: 1111px; height: 1200px; overflow: hidden; background: var(--paper); }
  .canvas { position: relative; width: 1111px; height: 1200px; overflow: hidden; }
  .page {
    position: absolute; left: 0; top: 0;
    width: 1148px; height: 1240px;
    transform: scale(0.9678); transform-origin: 0 0;
    background: var(--paper);
    font-family: "Michroma", sans-serif;
    color: var(--ink);
  }
  .backdrop { position: absolute; inset: 0; }

  .spine-fact {
    position: absolute; left: 406px; top: 84px; width: 560px;
    font-family: "Libre Baskerville", Georgia, serif; font-weight: 700;
    font-size: 28px; line-height: 40px; color: var(--white);
    white-space: nowrap;
  }

  .mini-month { position: absolute; left: 26px; top: 312px; width: 265px; }
  .mini-month__title { margin-left: 100px; font-size: 18px; font-variant: small-caps; letter-spacing: 1px; margin-bottom: 14px; font-weight: 400; }
  .mini-month__grid { display: grid; grid-template-columns: repeat(7, 38px); row-gap: 10px; font-size: 14px; }
  .mini-month__grid span { line-height: 21px; -webkit-text-stroke: 0.5px var(--ink); }
  .mini-month__grid .sun { color: var(--sunday); -webkit-text-stroke: 0.5px var(--sunday); }

  .month-head { position: absolute; left: 94px; top: 540px; display: flex; align-items: center; gap: 34px; }
  .month-head__name { font-size: 80px; color: var(--title); font-variant: small-caps; letter-spacing: 8px; line-height: 1; font-weight: 400; -webkit-text-stroke: 2px var(--title); }
  .brand-mark { display: flex; align-items: center; gap: 8px; margin-top: 10px; }
  .brand-mark__dot { width: 22px; height: 22px; border-radius: 50%; background: var(--badge); }
  .brand-mark__name { font-size: 24px; color: var(--badge); }

  .month-grid { position: absolute; left: 100px; top: 660px; width: 942px; }
  .month-grid__row { display: grid; grid-template-columns: repeat(7, 134.5px); }
  .month-grid__row--head { height: 40px; font-size: 24px; -webkit-text-stroke: 1px var(--ink); }
  .month-grid__row--week {
    height: 98px; align-items: end; padding-bottom: 6px;
    border-bottom: 2px solid var(--rule);
    font-size: 28px; -webkit-text-stroke: 1.2px var(--ink);
  }
  .month-grid__row--first { height: 95px; }
  .month-grid__row span.sun { color: var(--sunday); -webkit-text-stroke-color: var(--sunday); }

  .footnote { position: absolute; right: 22px; top: 1204px; font-family: "Open Sans", Arial, sans-serif; font-size: 20px; color: var(--ink); }
</style>
</head>
<body>
<div class="canvas">
  <div class="page">
    <svg class="backdrop" width="1148" height="1240" viewBox="0 0 1148 1240">
      <defs>
        <linearGradient id="photoTone" x1="0" y1="0" x2="1" y2="1">
          <stop offset="0" stop-color="#aaaaaa"/>
          <stop offset="1" stop-color="#7f7f7f"/>
        </linearGradient>
        <linearGradient id="vertebraTone" x1="0" y1="0" x2="1" y2="1">
          <stop offset="0" stop-color="#5d2462"/>
          <stop offset="1" stop-color="#4f1c53"/>
        </linearGradient>
      </defs>
      <path role="img" aria-label="Photograph of a man hunched over a laptop on a folding chair"
            d="M0 0 H1148 V720 C1060 560 900 470 700 390 C560 330 420 320 260 250 C150 200 60 130 0 70 Z"
            fill="url(#photoTone)"/>
      <path class="band band--light" d="M0 70 C60 130 150 200 260 250 C420 320 560 330 700 390 C900 470 1060 560 1148 720 V760 C1040 600 880 500 690 430 C540 370 400 360 240 290 C140 245 60 180 0 130 Z" fill="#9a5fa0"/>
      <path class="band band--mid" d="M0 95 C60 150 150 215 255 262 C415 332 555 345 695 405 C895 485 1055 580 1148 740 V752 C1045 590 885 495 692 418 C548 360 408 352 248 278 C145 232 62 168 0 118 Z" fill="#7b3f7f"/>
      <path role="img" aria-label="Illustration of a row of purple vertebrae along the spine band"
            d="M0 20 C80 60 170 130 270 180 C420 255 560 270 700 320 C900 395 1060 500 1148 640 L1130 720 C1040 560 880 470 690 410 C550 360 410 345 250 270 C150 220 60 150 0 110 Z"
            fill="url(#vertebraTone)"/>
    </svg>

    <p class="spine-fact">Spine Fact:<br>Sitting in a hunched<br>position puts 200 lbs of<br>pressure in your lumbar spine.</p>

    <section class="mini-month" aria-label="May 2018">
      <h2 class="mini-month__title">May</h2>
      <div class="mini-month__grid">
        <span>M</span><span>T</span><span>W</span><span>T</span><span>F</span><span>S</span><span class="sun">S</span>
        <span></span><span>1</span><span>2</span><span>3</span><span>4</span><span>5</span><span class="sun">6</span>
        <span>7</span><span>8</span><span>9</span><span>10</span><span>11</span><span>12</span><span class="sun">13</span>
        <span>14</span><span>15</span><span>16</span><span>17</span><span>18</span><span>19</span><span class="sun">20</span>
        <span>21</span><span>22</span><span>23</span><span>24</span><span>25</span><span>26</span><span class="sun">27</span>
        <span>28</span><span>29</span><span>30</span><span>31</span>
      </div>
    </section>

    <header class="month-head">
      <h1 class="month-head__name">June</h1>
      <div class="brand-mark"><span class="brand-mark__dot"></span><span class="brand-mark__name">FSW</span></div>
    </header>

    <section class="month-grid" aria-label="June 2018">
      <div class="month-grid__row month-grid__row--head">
        <span>M</span><span>T</span><span>W</span><span>T</span><span>F</span><span>S</span><span class="sun">S</span>
      </div>
      <div class="month-grid__row month-grid__row--week month-grid__row--first">
        <span></span><span></span><span></span><span></span><span>1</span><span>2</span><span class="sun">3</span>
      </div>
      <div class="month-grid__row month-grid__row--week">
        <span>4</span><span>5</span><span>6</span><span>7</span><span>8</span><span>9</span><span class="sun">10</span>
      </div>
      <div class="month-grid__row month-grid__row--week">
        <span>11</span><span>12</span><span>13</span><span>14</span><span>15</span><span>16</span><span class="sun">17</span>
      </div>
      <div class="month-grid__row month-grid__row--week">
        <span>18</span><span>19</span><span>20</span><span>21</span><span>22</span><span>23</span><span class="sun">24</span>
      </div>
      <div class="month-grid__row month-grid__row--week">
        <span>25</span><span>26</span><span>27</span><span>28</span><span></span><span></span><span></span>
      </div>
    </section>

    <p class="footnote">www.spinefsw.example.org</p>
  </div>
</div>
</body>
</html>
```